Harborline Auto LLC

Car Dealer Customer Service
Address: 2874 Cresthaven Road, Shelbyville, TN 37162
web: www.harborlineautoxq.net
email: harborlineautoxq@mailnest.example
Phone: (931) 555-0148
Phone: (629) 555-0173

```html
<!DOCTYPE html>
<html lang="en">
<head>
<meta charset="utf-8">
<title>Harborline Auto Business Card</title>
<link rel="stylesheet" href="https://fonts.googleapis.com/css2?family=Montserrat:wght@800&family=Poppins:wght@400;600&display=swap">
<style>
  :root {
    --backdrop: #2b2b2b;
    --card: #f1f1f0;
    --blue: #1b6e9c;
    --blue-bright: #2186bd;
    --gold: #e2a93b;
    --ink: #1f1f1f;
  }
  html, body {
    margin: 0;
    width: 1200px;
    height: 1138px;
    overflow: hidden;
    background: var(--backdrop);
  }
  .card {
    position: absolute;
    background: var(--card);
    border-radius: 14px;
    overflow: hidden;
    font-family: "Poppins", sans-serif;
    color: var(--ink);
  }
  .card-front { left: 274px; top: 186px; width: 622px; height: 376px; }
  .card-back  { left: 276px; top: 608px; width: 618px; height: 374px; }

  /* front */
  .front-decor {
    position: absolute; left: 300px; top: 0; width: 322px; height: 358px;
    background: linear-gradient(135deg, rgba(33,134,189,0.07), rgba(33,134,189,0.03));
  }
  .brand-mark {
    position: absolute; left: 50%; top: 112px;
    width: 74px; height: 74px; margin-left: -37px;
    border-radius: 50%; background: var(--blue-bright);
  }
  .front-name {
    position: absolute; left: 0; right: 0; top: 218px;
    text-align: center;
    font-family: "Montserrat", sans-serif; font-weight: 800;
    font-size: 29px; letter-spacing: 0.5px; color: var(--blue);
    margin: 0;
  }
  .front-web {
    position: absolute; left: 0; right: 0; top: 322px;
    display: flex; justify-content: center; align-items: center; gap: 22px;
    font-size: 15px;
  }
  .front-web .rule { width: 56px; height: 2px; background: var(--gold); }
  .front-band {
    position: absolute; left: 0; right: 0; bottom: 0; height: 18px;
    display: flex;
  }
  .front-band .half-blue { flex: 1; background: var(--blue); }
  .front-band .half-gold { flex: 1; background: var(--gold); }

  /* back */
  .back-decor {
    position: absolute; left: 384px; top: 0; width: 234px; height: 374px;
    background: linear-gradient(160deg, #2186bd 0%, #5aa3cc 45%, #e7b95c 100%);
  }
  .back-name {
    position: absolute; left: 28px; top: 42px; margin: 0;
    font-family: "Montserrat", sans-serif; font-weight: 800;
    font-size: 28px; letter-spacing: 0.5px; color: var(--blue);
  }
  .person { position: absolute; left: 28px; top: 150px; }
  .person-name { margin: 0; font-weight: 600; font-size: 23px; color: var(--blue); line-height: 1.1; }
  .person-role { margin: 3px 0 0; font-size: 15px; }
  .contact {
    position: absolute; left: 28px; top: 228px;
    list-style: none; margin: 0; padding: 0;
    font-size: 15px; line-height: 23px;
  }
  .contact li { display: flex; align-items: center; gap: 10px; white-space: nowrap; }
  .contact .phone { font-weight: 600; color: var(--blue); font-size: 17px; }
  .contact svg { width: 15px; height: 15px; fill: var(--gold); flex: none; }
  .contact .address { margin-top: 3px; }
</style>
</head>
<body>

<section class="card card-front">
  <div class="front-decor" role="img" aria-label="Faint enlarged brand emblem area"></div>
  <div class="brand-mark"></div>
  <h1 class="front-name">HARBORLINE AUTO</h1>
  <div class="front-web"><span class="rule"></span><span>www.harborlineautoxq.net</span><span class="rule"></span></div>
  <div class="front-band"><span class="half-blue"></span><span class="half-gold"></span></div>
</section>

<section class="card card-back">
  <div class="back-decor" role="img" aria-label="Large brand emblem area"></div>
  <h2 class="back-name">HARBORLINE AUTO</h2>
  <div class="person">
    <p class="person-name">Daniel Korvan</p>
    <p class="person-role">Managing Director</p>
  </div>
  <ul class="contact">
    <li class="phone"><svg viewBox="0 0 24 24"><path d="M6.6 10.8a15 15 0 0 0 6.6 6.6l2.2-2.2a1 1 0 0 1 1-.25 11.4 11.4 0 0 0 3.6.57 1 1 0 0 1 1 1V20a1 1 0 0 1-1 1A17 17 0 0 1 3 4a1 1 0 0 1 1-1h3.5a1 1 0 0 1 1 1c0 1.25.2 2.450.57 3.570a1 1 0 0 1-.25 1z"/></svg>931-555-0148</li>
    <li class="phone"><svg viewBox="0 0 24 24"><path d="M6.6 10.8a15 15 0 0 0 6.6 6.6l2.2-2.2a1 1 0 0 1 1-.25 11.4 11.4 0 0 0 3.6.57 1 1 0 0 1 1 1V20a1 1 0 0 1-1 1A17 17 0 0 1 3 4a1 1 0 0 1 1-1h3.5a1 1 0 0 1 1 1c0 1.25.2 2.450.57 3.570a1 1 0 0 1-.25 1z"/></svg>629-555-0173</li>
    <li><svg viewBox="0 0 24 24"><path d="M3 5h18a1 1 0 0 1 1 1v12a1 1 0 0 1-1 1H3a1 1 0 0 1-1-1V6a1 1 0 0 1 1-1zm1 2.4V17h16V7.4l-8 5.3z M5 7l7 4.6L19 7z"/></svg>www.harborlineautoxq.net</li>
    <li><svg viewBox="0 0 24 24"><path d="M12 2a10 10 0 1 0 0 20 10 10 0 0 0 0-20zm0 2a8 8 0 0 1 7.7 6H4.3A8 8 0 0 1 12 4zm-7.7 8h15.4a8 8 0 0 1-15.4 0z"/></svg>harborlineautoxq@mailnest.example</li>
    <li class="address">2874 Cresthaven Road, Shelbyville, TN 37162</li>
  </ul>
</section>

</body>
</html>
```